Talbrook Answering Service Brochure

Design a brochure for an answering service/call center based on the information submitted/attached. Photos and text will be included. Would like it designed to complement the logo provided. This brochure will explain to the potential customer who we are and what we have to offer.

The Talbrook representatives take and processes inbound calls, 24-7-365

Target Market(s)

Any business, however, primarily Medical, oil and gas, non profits, and the service industry

Industry/Entity Type

Telecommunications

Font styles to use
Serif
Other font styles liked:
• coordinate with logo

Requirements
Must have
• Modern, bright, bold and neatly structured brochure that will complement the logo and our brand.

```html
<!DOCTYPE html>
<html lang="en">
<head>
<meta charset="utf-8">
<title>Talbrook Answering Service Brochure</title>
<link rel="stylesheet" href="https://fonts.googleapis.com/css2?family=Fira+Sans:wght@400;600;700&family=Fira+Sans+Condensed:ital,wght@0,400;0,600;1,400;1,600&display=swap">
<style>
  :root {
    --bg: #c9c9c9;
    --paper: #ffffff;
    --paper-shade: #efefef;
    --ink: #2f2e33;
    --dark: #333136;
    --red: #d3232b;
    --text: #3a3a3f;
  }
  * { box-sizing: border-box; margin: 0; padding: 0; }
  html, body { width: 1200px; height: 1200px; overflow: hidden; background: var(--bg); }
  body { position: relative; font-family: "Fira Sans", sans-serif; color: var(--text); }

  .brochure {
    position: absolute; left: 45px; top: 200px;
    width: 1110px; height: 800px;
    display: flex;
    box-shadow: 0 10px 30px rgba(0,0,0,.18);
  }
  .panel {
    position: relative; width: 370px; height: 800px; overflow: hidden;
    background: linear-gradient(90deg, var(--paper) 0%, var(--paper) 78%, var(--paper-shade) 100%);
  }
  .panel svg.band { position: absolute; left: 0; width: 370px; display: block; }
  .band-top { top: 0; }
  .band-bottom { bottom: 0; }

  .bullets { list-style: none; }
  .bullets li { position: relative; }
  .bullets li::before { content: "·"; position: absolute; left: 0; font-style: normal; }

  /* Left panel */
  .panel--left { font-family: "Fira Sans Condensed", sans-serif; font-style: italic; }
  .panel--left .content { position: absolute; left: 34px; right: 30px; top: 150px; font-size: 12px; line-height: 1.45; }
  .panel--left .bullets li { padding-left: 26px; }
  .section-title { font-family: "Fira Sans Condensed", sans-serif; font-weight: 600; font-size: 20px; line-height: 1.2; color: var(--ink); margin: 24px 0 10px; white-space: nowrap; }
  .panel--left p { text-align: justify; }
  .lead-in { margin: 14px 0 8px; }

  /* Middle panel */
  .panel--middle .content { position: absolute; left: 32px; right: 26px; top: 118px; font-size: 12px; line-height: 1.45; }
  .panel--middle h2 { font-weight: 700; font-size: 18px; color: var(--ink); margin-bottom: 12px; }
  .panel--middle p { margin-bottom: 14px; }
  .panel--middle .bullets { margin-bottom: 14px; }
  .panel--middle .bullets li { padding-left: 32px; }
  .panel--middle .note { margin-bottom: 0; }

  .test-drive {
    position: absolute; left: 32px; right: 26px; top: 596px;
    border: 1.5px solid var(--red); border-radius: 12px 12px 0 0;
    padding: 22px 0 0; text-align: center; font-size: 12.5px; line-height: 1.4;
  }
  .test-drive .tab {
    position: absolute; top: -13px; left: 50%; transform: translateX(-50%);
    background: var(--dark); color: #fff; font-weight: 700; font-size: 15px; line-height: 1.5; padding: 0 18px; white-space: nowrap;
  }
  .test-drive .intro { padding: 0 14px; }
  .test-drive .contact { text-align: left; padding: 8px 0 8px 22px; line-height: 1.5; }
  .contact-row { display: flex; align-items: center; gap: 7px; }
  .contact-row svg { width: 12px; height: 12px; }
  .test-drive .strip { background: var(--red); color: #fff; padding: 4px 0; font-size: 13px; white-space: nowrap; margin: 0 -1.5px; }
  .test-drive .tagline { color: var(--red); padding: 4px 0 5px; font-size: 14px; }

  /* Right panel */
  .photo {
    position: absolute; left: 0; top: 150px; width: 370px; height: 460px;
    background: radial-gradient(ellipse at 60% 45%, #e9d2c4 0%, #d9dde2 45%, #eef0f2 100%);
  }
  .bubble {
    position: absolute; right: 26px; top: 62px; width: 130px; height: 130px; border-radius: 50%;
    background: var(--dark); border: 4px solid #fff; box-shadow: 0 0 0 1.5px #bbb;
    color: #fff; font-size: 13px; line-height: 1.3; text-align: center;
    display: flex; align-items: center; justify-content: center; padding: 14px;
  }
  .bubble::after {
    content: ""; position: absolute; left: 20px; bottom: -12px;
    border-left: 12px solid transparent; border-right: 7px solid transparent; border-top: 18px solid var(--dark);
  }
  .brand { position: absolute; right: 30px; bottom: 58px; text-align: center; color: var(--ink); }
  .brand .mark { width: 40px; height: 40px; border-radius: 50%; background: var(--red); margin: 0 auto 8px; }
  .brand .name { font-weight: 700; font-size: 34px; line-height: 1; letter-spacing: .5px; }
  .brand .sub { font-weight: 700; font-size: 11px; letter-spacing: 1.2px; text-transform: uppercase; margin-top: 2px; }
  .brand .est { font-weight: 700; font-size: 9px; letter-spacing: 1px; }
</style>
</head>
<body>
<main class="brochure">

  <section class="panel panel--left">
    <svg class="band band-top" viewBox="0 0 370 140" height="140" aria-hidden="true">
      <path d="M0 0H370V70Q190 80 0 135Z" fill="var(--dark)"/>
      <path d="M0 135Q190 80 370 70V82Q190 92 0 140Z" fill="var(--red)"/>
    </svg>
    <div class="content">
      <ul class="bullets">
        <li>Call Routing &amp; Transfer</li>
        <li>Web Integration</li>
        <li>Database Interaction</li>
        <li>Text Messaging</li>
        <li>Alpha Paging</li>
        <li>Email</li>
        <li>Fax</li>
        <li>Combination Service – Utilize our reliable voice mail system with an operator revert functionality. Your callers have the option of pressing “0” for a representative at any time.</li>
      </ul>
      <h2 class="section-title">Call Center Services Done Right</h2>
      <p>Talbrook is a complete call center provider. We train our representatives to follow your business protocol and then they are able to work as an autonomous unit that only requires your attention if you wish to change a procedure. Our call center representatives handle everything from pre-qualification to appointment setting and order taking. The Clear Response team is your team.</p>
      <p class="lead-in">Our call center services include:</p>
      <ul class="bullets">
        <li>Order Taking (on your site or our system)</li>
        <li>Pre-Qualification</li>
        <li>Help Desk</li>
        <li>Appointment Setting</li>
        <li>Appointment Confirmation</li>
        <li>Lead Generation</li>
        <li>Order Processing</li>
      </ul>
    </div>
    <svg class="band band-bottom" viewBox="0 0 370 70" height="70" aria-hidden="true">
      <path d="M0 12Q180 0 370 62V70H0Z" fill="var(--red)"/>
      <path d="M0 26Q180 14 370 70H0Z" fill="var(--dark)"/>
    </svg>
  </section>

  <section class="panel panel--middle">
    <svg class="band band-top" viewBox="0 0 370 100" height="100" aria-hidden="true">
      <rect width="370" height="100" fill="var(--dark)"/>
      <path d="M0 72L370 60V100H0Z" fill="var(--red)"/>
      <path d="M0 96L370 90V100H0Z" fill="var(--paper)"/>
    </svg>
    <div class="content">
      <h2>Special Services</h2>
      <p>Medical Answering Services – Clear Response representatives understand the unique needs of the medical community and are trained to provide the support you need.</p>
      <ul class="bullets">
        <li>HIPAA compliant messaging system</li>
        <li>Medical messages stored securely for 1 year</li>
        <li>Disaster Recovery – stay in contact with employees, management and customers in the event of emergency</li>
      </ul>
      <p>Oil and Gas – We serve many clients in the Energy industry and our representatives are well-versed in handling customer relations in what can be a demanding field.</p>
      <p>Commercial Property Management – Our representatives have experience maintaining positive relations with tenants, property managers and other real estate personnel.</p>
      <p class="note">*Ask one of our representatives about custom solutions for your industry</p>
    </div>
    <div class="test-drive">
      <span class="tab">Test Drive</span>
      <p class="intro">There’s no better way to get a feel for our services than by speaking with one of our own representatives – 800.555.CLEAR.</p>
      <div class="contact">
        <div class="contact-row">
          <svg viewBox="0 0 16 16" aria-hidden="true"><circle cx="8" cy="8" r="7" fill="none" stroke="var(--red)" stroke-width="1.2"/><path d="M5 4.5l1.5 0 .8 2-1 .8a5 5 0 002.4 2.4l.8-1 2 .8v1.5a1 1 0 01-1 1A7 7 0 014 5.5a1 1 0 011-1z" fill="var(--red)"/></svg>
          <span>(800)555-0142, (555) 010-3113</span>
        </div>
        <div class="contact-row">
          <svg viewBox="0 0 16 16" aria-hidden="true"><g fill="none" stroke="var(--red)" stroke-width="1.2"><circle cx="8" cy="8" r="7"/><ellipse cx="8" cy="8" rx="3" ry="7"/><path d="M1 8h14M2 4.5h12M2 11.5h12"/></g></svg>
          <span>www.talbrooksvc.com</span>
        </div>
      </div>
      <div class="strip">Subscribe to a Great Service, and a Strong ROI!</div>
      <div class="tagline">Any Call—Any Time—Any Place</div>
    </div>
  </section>

  <section class="panel panel--right">
    <div class="photo" role="img" aria-label="Photo of a smiling call center representative wearing a headset"></div>
    <svg class="band band-top" viewBox="0 0 370 180" height="180" aria-hidden="true">
      <path d="M0 0H370V150L0 115Z" fill="var(--dark)"/>
      <path d="M0 115L370 150V172L0 130Z" fill="var(--red)"/>
      <path d="M0 130L370 172V180H0Z" fill="var(--paper)"/>
    </svg>
    <div class="bubble">Automated or Live – Answering Services That Work for You</div>
    <svg class="band" style="top:560px" viewBox="0 0 370 110" height="110" aria-hidden="true">
      <path d="M0 70Q200 -10 370 60V110H0Z" fill="var(--paper)"/>
      <path d="M0 40Q200 -20 370 50V60Q200 -10 0 90Z" fill="var(--dark)"/>
    </svg>
    <div class="brand">
      <div class="mark" aria-hidden="true"></div>
      <div class="name">TALBROOK</div>
      <div class="sub">Answering Service</div>
      <div class="est">EST. 1932</div>
    </div>
  </section>

</main>
</body>
</html>
```